Business card design for new eCommerce site focusing on integrity and strong businsess tactics

We need a business card that will stand out and be memorable. Something with color that matches our company logo colors. Think high end version of Pactivo. There are 2 logos provided. The parent company is called Amber Ledge Partners and we are presenting a new and very exciting eCommerce site called BrightHarborTrade.example.

Target Market(s)

Our target markets are in the Activities, Food and Beverage, Health and Beauty

Industry/Entity Type

Marketing

Contact Information for Business Card

We have 4 members that need cards...I will provide all info to the winner of the design contest
Business Address is
4870 West 63rd Avenue, Suite C207
Phoenix AZ 85731

Font styles to use
Serif
Sans Serif

Colors

Designer to choose colors to be used in the design.

Requirements
Must have
• The card must be memorable...should be unique in design but must exude integrity and be playful .
• I have provided several colors or our parent company...please feel free to use which ever
Nice to have
• I will leave this up to you. Feel free to use other images of your choosing that wraps around our client.....Activities, Dining, Health, Beauty
Should not have
• just dont be boring

```html
<!DOCTYPE html>
<html lang="en">
<head>
<meta charset="utf-8">
<title>BrightHarborTrade.example – Business Card</title>
<link rel="stylesheet" href="https://fonts.googleapis.com/css2?family=Didact+Gothic&family=Nunito+Sans:wght@700;800&display=swap">
<style>
  :root {
    --backdrop: #2a2a2a;
    --card-white: #f4f4f4;
    --brand-blue: #2b78a8;
    --brand-green: #8cc63f;
    --badge-green: #9cc43e;
    --text-grey: #4a4a4a;
  }
  * { margin: 0; padding: 0; box-sizing: border-box; }
  html, body { width: 1200px; height: 960px; overflow: hidden; }
  body {
    position: relative;
    background: var(--backdrop);
    font-family: "Didact Gothic", "Century Gothic", sans-serif;
  }
  .card {
    position: absolute;
    width: 600px;
    height: 342px;
    overflow: hidden;
  }
  .card--front { left: 314px; top: 113px; background: var(--card-white); }
  .card--back { left: 311px; top: 472px; background: var(--brand-blue); }

  .brand {
    position: absolute;
    left: 34px;
    top: 58px;
    display: flex;
    align-items: center;
    gap: 8px;
  }
  .brand__dot {
    width: 18px; height: 18px; border-radius: 50%;
    background: var(--brand-green);
  }
  .brand__name {
    font-family: "Nunito Sans", sans-serif;
    font-weight: 700;
    font-size: 20px;
    color: var(--brand-blue);
    letter-spacing: -0.3px;
  }
  .brand__tagline {
    position: absolute;
    left: 99px;
    top: 84px;
    font-size: 12px;
    color: var(--text-grey);
    letter-spacing: 0.6px;
  }
  .emblem-area {
    position: absolute;
    left: 341px; top: 8px;
    width: 255px; height: 320px;
    border-radius: 40px;
    background: radial-gradient(ellipse at 50% 45%, rgba(140,198,63,0.35) 0%, rgba(43,120,168,0.22) 55%, rgba(244,244,244,0) 80%);
  }
  .edge-tab {
    position: absolute;
    left: -14px; top: 136px;
    width: 28px; height: 40px;
    border-radius: 50%;
    background: var(--brand-blue);
  }
  .person { position: absolute; left: 53px; top: 135px; }
  .person__name {
    font-family: "Nunito Sans", sans-serif;
    font-weight: 800;
    font-size: 21px;
    color: var(--brand-blue);
    letter-spacing: 0.3px;
    line-height: 24px;
  }
  .person__role {
    font-size: 15px;
    color: var(--brand-green);
    line-height: 20px;
  }
  .address {
    position: absolute; left: 52px; top: 187px;
    font-size: 14.5px; line-height: 18px; color: var(--text-grey);
  }
  .contacts {
    position: absolute; left: 53px; top: 232px;
    list-style: none;
  }
  .contacts li {
    display: flex; align-items: center; gap: 8px;
    font-size: 14.5px; line-height: 19px; color: var(--text-grey);
  }
  .contacts svg { width: 13px; height: 13px; fill: var(--brand-blue); }

  .badge {
    position: absolute;
    left: 227px; top: 70px;
    width: 146px; height: 146px;
    border-radius: 50%;
    background: var(--badge-green);
  }
  .parent-name {
    position: absolute;
    left: 0; right: 0; top: 222px;
    text-align: center;
    font-family: "Nunito Sans", sans-serif;
    font-weight: 700;
    font-size: 33px;
    color: var(--badge-green);
  }
</style>
</head>
<body>
  <section class="card card--front">
    <div class="brand">
      <span class="brand__dot"></span>
      <span class="brand__name">BrightHarborTrade.example</span>
    </div>
    <p class="brand__tagline">Activities-Dining-Health-Beauty</p>
    <div class="emblem-area" role="img" aria-label="Large brand emblem in green and blue"></div>
    <span class="edge-tab"></span>

    <div class="person">
      <h1 class="person__name">JORDAN ELLIS</h1>
      <p class="person__role">CEO/FOUNDER</p>
    </div>
    <p class="address">4870 West 63rd Avenue<br>Suite C207, Phoenix AZ 85731</p>
    <ul class="contacts">
      <li><svg viewBox="0 0 16 16"><path d="M3.6 1l2.6 3-1.4 1.8c.9 2 2.4 3.5 4.4 4.4L11 8.8l3 2.6-1.6 2.6C6.6 13.8 2.2 9.4 1 3.6z"/></svg>555 014 2763</li>
      <li><svg viewBox="0 0 16 16"><path d="M4 0h8v16H4zM5.5 2v10h5V2zM7 13.3h2v1.4H7z" fill-rule="evenodd"/></svg>555 019 4871</li>
      <li><svg viewBox="0 0 16 16"><path d="M1 3h14v10H1zM2.5 4.5 8 9l5.5-4.5v7h-11z" fill-rule="evenodd"/></svg>jordan@brightharbortrade.example</li>
      <li><svg viewBox="0 0 16 16"><path d="M8 1a7 7 0 1 0 0 14A7 7 0 0 0 8 1zm0 1.6c1 1.2 1.6 2.8 1.7 4.6H6.3C6.4 5.4 7 3.8 8 2.6zM6.3 8.8h3.4C9.6 10.6 9 12.2 8 13.4 7 12.2 6.4 10.6 6.3 8.8z" fill-rule="evenodd"/></svg>www.brightharbortrade.example</li>
    </ul>
  </section>

  <section class="card card--back">
    <span class="badge"></span>
    <h2 class="parent-name">Amber Ledge Partners</h2>
  </section>
</body>
</html>
```